1. Overview of company:
Teal Q Amber Mobile solutions private Ltd is one of the leading innovators & providers of Value added services (VAS) and telecom solutions to the top telecom operators across the world. We are the pioneer of several telecom technologies and products with our solutions empowering over 40 telecom giant in 51 countries.

2. Product Overview:
Zippy tone is the most innovative voice morphing mobile app that has revolutionized the concept of IVR based offerings for telecom operators across the world. It lets you talk to your friend in a voice of your choice at just the press of a button. In addition to every call, users can now speak to their friends with background sounds of their choice.

In simple words: If person A calls person B, person A can choose the voice he wants B to listen, Words and sentences remain same just the voice changes. Person A can even activate a background sound for both of them while talking.

3. Objective of the design:
The purpose of this campaign is to establish Zippy tone as Innovative, Lively, Youthful, Fun mobile app generally used for spreading smiles via pranks. The primary objective is to persuade the audience to download and use Zippy Tone mobile app, as well as to spread and characterize this new app.

4. Product layout:
Page 1: Landing Page
- pictorial explanation, what Zippy Tone stands for

Page 2: Home Screen options
-Navigation to zippy tone
-Navigation to zippy backdrop

Page 3: Zippy Tone options
-Female
-Cartoon
-King
-Bunny

Page 4: Zippy backdrop options
-Romantic
-Airport
-Traffic
-Football
-Church
-Beach

5. Target Audience
The users of the mobile app will be teenager whose age ranges from 16-27. The demographics are not restricted to a particular country and will be present on global level.

6. Deliverable
- 4 Uncoded screen and icon for mobile app "Zippy Tone"
- Our company name is "Teal Q amber" , we would like to see designs that use Black and Green, at the same time its not mandatory.
-Design should communicate what the app stands for "Changing voice of caller"

Target Market(s)

User of the mobile app will be teenagers whose age ranges from 16-27. The demographics are not restricted to a particular country and will be present on global level. It's for masses.

Industry/Entity Type

Telecommunications

Requirements
Must have
• The design should be self explanatory, what the app stands for.
• Editable format for integration purpose.
Nice to have
• Would prefer Icons and very few words.
• Professional, elegant at the same time trendy designs.

```html
<!DOCTYPE html>
<html lang="en">
<head>
<meta charset="utf-8">
<title>Zippy Backdrop options</title>
<link rel="stylesheet" href="https://fonts.googleapis.com/css2?family=Patrick+Hand&family=Raleway:wght@300&display=swap">
<style>
  :root {
    --green: #8fc03c;
    --green-dark: #7fae30;
    --band-grey: #ededed;
    --sub-grey: #a6a6a6;
    --label-grey: #555555;
    --rule: #bdbdbd;
    --white: #ffffff;
    --heart-pink: #f3b3c6;
    --plane-blue: #cfe0ee;
    --road-grey: #5a5a5a;
    --ball-dark: #4a4a4a;
    --church-tan: #c7b8a3;
    --beach-orange: #f7b232;
  }
  * { margin: 0; padding: 0; box-sizing: border-box; }
  html, body { width: 676px; height: 1200px; overflow: hidden; background: var(--white); }
  .screen { position: relative; width: 676px; height: 1200px; background: var(--white); }

  .header { position: absolute; left: 0; top: 0; width: 676px; height: 205px; }
  .header svg { position: absolute; left: 0; top: 0; }
  .back-arrow { position: absolute; left: 38px; top: 66px; width: 34px; height: 44px; }
  .screen-title {
    position: absolute; left: 118px; top: 52px;
    font-family: "Patrick Hand", cursive; font-size: 48px; color: var(--white);
    letter-spacing: 1px; font-weight: 400;
  }
  .screen-hint {
    position: absolute; left: 0; top: 155px; width: 676px; text-align: center;
    font-family: "Raleway", sans-serif; font-weight: 300; font-size: 25px; color: var(--sub-grey);
  }

  .ambiance-list { position: absolute; left: 0; top: 265px; width: 676px; list-style: none; }
  .ambiance-option {
    position: relative; display: flex; align-items: center;
    border-bottom: 1.5px solid var(--rule);
  }
  .ambiance-icon { position: absolute; left: 40px; width: 88px; height: 80px; }
  .ambiance-label {
    position: absolute; left: 190px;
    font-family: "Patrick Hand", cursive; font-size: 52px; color: var(--label-grey);
  }
  .radio { position: absolute; left: 582px; width: 52px; height: 52px; }

  .save-button {
    position: absolute; left: 221px; top: 1010px; width: 233px; height: 73px;
    font-family: "Patrick Hand", cursive; font-size: 48px; color: var(--white);
    display: flex; align-items: center; justify-content: center; letter-spacing: 1px;
  }
  .save-button svg { position: absolute; left: 0; top: 0; }
  .save-button span { position: relative; }
</style>
</head>
<body>
<main class="screen">
  <header class="header">
    <svg width="676" height="205" viewBox="0 0 676 205">
      <path d="M0 140 Q120 150 260 146 T520 150 T676 146 L676 205 Q540 196 400 200 T140 198 T0 202 Z" fill="var(--band-grey)"/>
      <path d="M0 0 H676 V150 Q560 140 420 146 T160 144 T0 148 Z" fill="var(--green)"/>
    </svg>
    <svg class="back-arrow" viewBox="0 0 34 44">
      <path d="M28 6 L8 22 L28 38" fill="none" stroke="var(--white)" stroke-width="6" stroke-linecap="round" stroke-linejoin="round"/>
    </svg>
    <h1 class="screen-title">Zippy Backdrop options</h1>
    <p class="screen-hint">select the ambiance that you want to talk</p>
  </header>

  <ul class="ambiance-list">
    <li class="ambiance-option" style="height:120px">
      <div class="ambiance-icon" role="img" aria-label="Illustration of pink hearts" style="top:20px;background:var(--heart-pink);border-radius:40%;opacity:.7"></div>
      <span class="ambiance-label" style="top:26px">Romantic</span>
      <svg class="radio" style="top:34px" viewBox="0 0 52 52"><circle cx="26" cy="26" r="23" fill="none" stroke="var(--green)" stroke-width="3"/><circle cx="26" cy="26" r="17" fill="var(--green)"/></svg>
    </li>
    <li class="ambiance-option" style="height:132px">
      <div class="ambiance-icon" role="img" aria-label="Illustration of an airplane" style="top:26px;background:var(--plane-blue);border-radius:40%"></div>
      <span class="ambiance-label" style="top:32px">Airport</span>
      <svg class="radio" style="top:40px" viewBox="0 0 52 52"><circle cx="26" cy="26" r="23" fill="none" stroke="var(--green)" stroke-width="3"/></svg>
    </li>
    <li class="ambiance-option" style="height:124px">
      <div class="ambiance-icon" role="img" aria-label="Illustration of a road with lane marks" style="top:22px;background:linear-gradient(90deg,var(--road-grey) 0 6%,transparent 6% 45%,var(--beach-orange) 45% 53%,transparent 53% 94%,var(--road-grey) 94%);opacity:.6"></div>
      <span class="ambiance-label" style="top:30px">Traffic</span>
      <svg class="radio" style="top:36px" viewBox="0 0 52 52"><circle cx="26" cy="26" r="23" fill="none" stroke="var(--green)" stroke-width="3"/></svg>
    </li>
    <li class="ambiance-option" style="height:106px">
      <div class="ambiance-icon" role="img" aria-label="Illustration of a football" style="top:14px;left:48px;width:74px;height:74px;background:var(--ball-dark);border-radius:50%"></div>
      <span class="ambiance-label" style="top:20px">Football</span>
      <svg class="radio" style="top:28px" viewBox="0 0 52 52"><circle cx="26" cy="26" r="23" fill="none" stroke="var(--green)" stroke-width="3"/></svg>
    </li>
    <li class="ambiance-option" style="height:104px">
      <div class="ambiance-icon" role="img" aria-label="Illustration of a small church" style="top:10px;left:38px;width:80px;background:var(--church-tan);border-radius:30% 30% 4px 4px"></div>
      <span class="ambiance-label" style="top:20px">Church</span>
      <svg class="radio" style="top:26px" viewBox="0 0 52 52"><circle cx="26" cy="26" r="23" fill="none" stroke="var(--green)" stroke-width="3"/></svg>
    </li>
    <li class="ambiance-option" style="height:105px">
      <div class="ambiance-icon" role="img" aria-label="Illustration of a beach with an umbrella" style="top:12px;background:var(--beach-orange);border-radius:45% 45% 40% 40%"></div>
      <span class="ambiance-label" style="top:20px">Beach</span>
      <svg class="radio" style="top:28px" viewBox="0 0 52 52"><circle cx="26" cy="26" r="23" fill="none" stroke="var(--green)" stroke-width="3"/></svg>
    </li>
  </ul>

  <div class="save-button" role="button">
    <svg width="233" height="73" viewBox="0 0 233 73"><path d="M6 4 Q116 0 228 2 Q233 36 230 70 Q116 74 4 72 Q0 36 6 4 Z" fill="var(--green)"/></svg>
    <span>SAVE</span>
  </div>
</main>
</body>
</html>
```